Alapca breeding needs a website

Presentation of the farm, animals (stallions, mares, information about the animals, for sale) and possible later expansion with a webshop (alpaca wool products). We want to present our farm and the animals on the farm on this page. A mission why we are doing this. Furthermore, each animal should be shown with a picture and described. Later we want to sell our own products made from alpaca wool via a webshop. But we still need to grow a bit to do that.

Target Market(s)

Information about my alpaca breeding and the alpaca farm

Industry/Entity Type

Tierzucht

Number of Pages Required

1 page

Font styles to use
Sans Serif

Requirements
Must have
• Modern design that matches the logo
Nice to have
• Intuitive operation / Clear structure
Should not have
• No

```html
<!DOCTYPE html>
<html lang="en">
<head>
<meta charset="utf-8">
<title>Meadowvale Alpacas</title>
<link href="https://fonts.googleapis.com/css2?family=Josefin+Sans:wght@400;600;700&display=swap" rel="stylesheet">
<style>
:root{
  --navy:#0c2442;
  --navy-deep:#081a31;
  --green:#8cc63f;
  --green-dark:#6ea52a;
  --text:#2b2f36;
  --muted:#555b63;
  --white:#ffffff;
  --black:#111111;
}
*{box-sizing:border-box;margin:0;padding:0}
html,body{width:1200px;height:5019px;overflow:hidden}
body{position:relative;font-family:"Josefin Sans",Arial,sans-serif;color:var(--text);background:var(--white)}
.abs{position:absolute}
.photo{position:absolute;border-radius:4px}
.btn{position:absolute;display:inline-flex;align-items:center;justify-content:center;background:var(--green);color:var(--navy);font-size:12px;font-weight:700;letter-spacing:.5px;text-transform:uppercase;border-radius:3px;height:40px;padding:0 22px}
.eyebrow{color:var(--green);font-size:17px;font-weight:700;letter-spacing:1px;text-transform:uppercase}
.heading{color:var(--navy);font-weight:700;line-height:1.15}
.body-copy{font-size:13.5px;line-height:1.65;color:var(--muted)}

/* hero */
.hero{position:absolute;left:0;top:0;width:1200px;height:820px;background:linear-gradient(180deg,#d7dbe6 0%,#c9cfdc 40%,#b89c78 62%,#7e5b3c 80%,#6b7f4c 100%)}
.hero-curve{position:absolute;left:0;top:700px;width:1200px;height:130px}
.nav{position:absolute;top:52px;left:0;width:1200px;height:30px}
.brand{position:absolute;left:120px;top:-10px;display:flex;align-items:center;gap:8px;color:var(--navy);font-weight:700;font-size:20px;letter-spacing:1px}
.brand .dot{width:14px;height:14px;border-radius:50%;background:var(--green)}
.nav-links{position:absolute;left:310px;top:6px;display:flex;gap:0;font-size:13px;color:var(--navy);font-weight:600}
.nav-links span{width:180px;text-align:center}
.nav-links span:first-child{width:0;margin-right:0}
.hero-title{position:absolute;top:140px;left:0;width:1200px;text-align:center;font-size:48px;font-weight:700;color:var(--navy);line-height:1.15}
.hero-text{position:absolute;top:270px;left:225px;width:750px;text-align:center;font-size:14px;line-height:1.65;color:#2a3140}
.scroll{position:absolute;left:586px;top:785px;width:28px;height:44px;border-radius:14px;background:var(--green)}
.scroll::after{content:"";position:absolute;left:12px;top:9px;width:4px;height:10px;border-radius:2px;background:var(--white)}

/* about */
.accent-green{position:absolute;background:var(--green)}
.accent-navy{position:absolute;background:var(--navy)}
</style>
</head>
<body>

<!-- HERO -->
<section class="hero" role="img" aria-label="Row of white, fawn and brown alpacas against a soft grey sky"></section>
<svg class="hero-curve" viewBox="0 0 1200 130" preserveAspectRatio="none"><path d="M0 60 Q600 130 1200 40 L1200 130 L0 130 Z" fill="#fff"/></svg>
<header class="nav">
  <div class="brand"><span class="dot"></span>MEADOWVALE</div>
  <nav class="nav-links">
    <span></span><span style="margin-left:-10px">HOME</span><span>ABOUT US</span><span>ANIMALS</span><span>SHOP</span><span>INQUIRE NOW</span>
  </nav>
  <svg class="abs" style="left:975px;top:4px" width="70" height="22" viewBox="0 0 70 22">
    <path d="M2 4h4l3 10h10l3-7H8" fill="none" stroke="#8cc63f" stroke-width="2"/>
    <circle cx="11" cy="18" r="1.8" fill="#8cc63f"/><circle cx="18" cy="18" r="1.8" fill="#8cc63f"/>
    <line x1="34" y1="3" x2="34" y2="19" stroke="#8cc63f" stroke-width="1.5"/>
    <circle cx="48" cy="10" r="6" fill="none" stroke="#8cc63f" stroke-width="2"/>
    <line x1="52.5" y1="14.5" x2="57" y2="19" stroke="#8cc63f" stroke-width="2"/>
  </svg>
</header>
<h1 class="hero-title">Indulge in the Softness<br>of Alpaca Wool</h1>
<p class="hero-text">Welcome to Meadowvale Alpacas, a picturesque haven nestled. Our farm is dedicated to raising and caring for a variety of animals, with a special focus on our beloved alpacas. We are passionate about sustainable farming and animal welfare, and we strive to create a harmonious environment where both our animals and our community can thrive.</p>
<div class="scroll"></div>

<!-- ABOUT -->
<section class="about">
  <div class="accent-green" style="left:115px;top:950px;width:70px;height:60px"></div>
  <div class="accent-navy" style="left:505px;top:950px;width:70px;height:60px"></div>
  <div class="accent-navy" style="left:115px;top:1390px;width:60px;height:110px"></div>
  <div class="photo" style="left:125px;top:960px;width:222px;height:255px;background:linear-gradient(160deg,#9fc4e6,#6c8a5a 70%,#4e5b3a)" role="img" aria-label="Woman with a grey horse in a field"></div>
  <div class="photo" style="left:368px;top:960px;width:200px;height:255px;background:linear-gradient(160deg,#7a7f86,#c9b79a 55%,#6b3b38)" role="img" aria-label="Man holding a fluffy alpaca lamb"></div>
  <div class="photo" style="left:125px;top:1235px;width:277px;height:255px;background:linear-gradient(180deg,#8fbfe8,#e8eef3 45%,#6fa04a 75%)" role="img" aria-label="White alpaca on green grass"></div>
  <div class="photo" style="left:423px;top:1235px;width:145px;height:255px;background:linear-gradient(170deg,#9db06a,#7a4a2a 55%,#4a2a18)" role="img" aria-label="Brown horse portrait"></div>

  <div class="eyebrow abs" style="left:711px;top:937px">About Us</div>
  <h2 class="heading abs" style="left:711px;top:963px;font-size:42px">Nurturing Farm<br>Animals with Love<br>and Care</h2>
  <p class="body-copy abs" style="left:711px;top:1128px;width:370px">Lorem Ipsum is simply dummy text of the printing and typesetting industry. Lorem Ipsum has been the industry's standard dummy text ever since the 1500s, when an unknown printer took a galley of type and scrambled it to make a type specimen book. It has survived not only five centuries, but also the leap into electronic typesetting, remaining essentially unchanged.</p>
  <p class="body-copy abs" style="left:711px;top:1325px;width:370px">It was popularised in the 1960s with the release of Lettersheet sheets containing Lorem Ipsum passages, and more recently with desktop publishing software like PageSetter including versions of Lorem Ipsum.</p>
  <div class="btn" style="left:711px;top:1470px">Read more about farm</div>
</section>

<!-- MISSION -->
<section class="mission">
  <div class="eyebrow abs" style="left:125px;top:1617px">Our Mission</div>
  <h2 class="heading abs" style="left:125px;top:1645px;font-size:42px">Happy Animals,<br>Healthy Farms</h2>
  <p class="body-copy abs" style="left:125px;top:1760px;width:360px">Lorem Ipsum is simply dummy text of the printing and typesetting industry. Lorem Ipsum has been the industry's standard dummy text ever since the 1500s, when an unknown printer took a galley of type and scrambled it to make a type specimen book. It has survived not only five centuries, but also the leap into electronic typesetting, remaining essentially unchanged.</p>
  <div class="btn" style="left:125px;top:1972px">The Animals</div>

  <div class="photo" style="left:540px;top:1635px;width:170px;height:370px;background:linear-gradient(170deg,#a7c2d8,#7a8e5a 50%,#5a4630);box-shadow:0 4px 14px rgba(0,0,0,.2)" role="img" aria-label="Horse grazing by a fence"></div>
  <div class="photo" style="left:665px;top:1625px;width:195px;height:375px;background:linear-gradient(175deg,#b5d0ea,#e0e6ea 30%,#7aa24b 60%,#4d6b30);border:6px solid #fff;box-shadow:0 4px 14px rgba(0,0,0,.2)" role="img" aria-label="Foal standing in a pasture"></div>
  <div class="photo" style="left:795px;top:1660px;width:295px;height:310px;background:linear-gradient(180deg,#8ab5de,#cfe0ee 40%,#8fae4c 60%,#5e8a2e);border:8px solid #fff;box-shadow:0 6px 18px rgba(0,0,0,.25)" role="img" aria-label="Red barn behind green farmland"></div>
  <svg class="abs" style="left:652px;top:1798px" width="36" height="36" viewBox="0 0 36 36"><circle cx="18" cy="18" r="17" fill="#8cc63f" stroke="#fff" stroke-width="2"/><path d="M21 11l-7 7 7 7" fill="none" stroke="#fff" stroke-width="2.5"/></svg>
  <svg class="abs" style="left:1068px;top:1798px" width="36" height="36" viewBox="0 0 36 36"><circle cx="18" cy="18" r="17" fill="#8cc63f" stroke="#fff" stroke-width="2"/><path d="M15 11l7 7-7 7" fill="none" stroke="#fff" stroke-width="2.5"/></svg>
</section>

<!-- MEET OUR ANIMALS -->
<section class="meet">
  <div class="abs" style="left:0;top:2195px;width:1200px;height:905px;background:linear-gradient(180deg,#e4ecf6 0%,#c9d9ec 18%,#8fb1d6 30%,#b8b09a 45%,#8b7a55 58%,#4f6a73 70%,#7a6a52 85%,#9a8a6e 100%)" role="img" aria-label="Alpacas grazing beside a mountain stream under a blue sky"></div>
  <svg class="abs" style="left:0;top:2190px" width="1200" height="90" viewBox="0 0 1200 90" preserveAspectRatio="none"><path d="M0 0 L1200 0 L1200 8 Q600 110 0 8 Z" fill="#fff"/></svg>
  <svg class="abs" style="left:0;top:3020px" width="1200" height="85" viewBox="0 0 1200 85" preserveAspectRatio="none"><path d="M0 80 Q600 -10 1200 80 L1200 85 L0 85 Z" fill="#fff"/></svg>
  <h2 class="heading abs" style="left:0;top:2265px;width:1200px;text-align:center;font-size:42px">Meet our Animals</h2>
  <p class="body-copy abs" style="left:235px;top:2330px;width:730px;text-align:center;color:#2a3140">Lorem Ipsum is simply dummy text of the printing and typesetting industry. Lorem Ipsum has been the industry's standard dummy text ever since the 1500s, when an unknown printer took a galley of type and scrambled it to make a type specimen book. It has survived not only five centuries, but also the leap into electronic typesetting, remaining essentially unchanged.</p>
  <p class="body-copy abs" style="left:235px;top:2440px;width:730px;text-align:center;color:#2a3140">It was popularised in the 1960s with the release of Lettersheet sheets containing Lorem Ipsum passages, and more recently with desktop publishing software like PageSetter including versions of Lorem Ipsum.</p>
  <div class="btn" style="left:528px;top:2540px;width:144px">Read more</div>

  <div class="abs" style="left:383px;top:2935px;width:520px;height:190px;background:#fff;border-radius:12px;box-shadow:0 6px 24px rgba(0,0,0,.15);padding:32px 40px;font-size:16px;line-height:1.75;color:var(--navy)">
    <div><b>Name:</b> Alpaca Name</div>
    <div><b>Age:</b> Age</div>
    <div><b>Breed:</b> Breed</div>
    <div><b>Description:</b> Brief description of the Alpaca's personality, traits, and any notable achievements.</div>
  </div>
  <svg class="abs" style="left:812px;top:2970px" width="38" height="38" viewBox="0 0 38 38"><circle cx="19" cy="19" r="16" fill="none" stroke="#8cc63f" stroke-width="2.5"/><path d="M13 25L25 13M16 13h9v9" fill="none" stroke="#8cc63f" stroke-width="2.5"/></svg>
</section>

<!-- FOR SALE -->
<section class="sale">
  <div class="eyebrow abs" style="left:0;top:3228px;width:1200px;text-align:center">The Alpaca Farm</div>
  <h2 class="heading abs" style="left:0;top:3255px;width:1200px;text-align:center;font-size:42px">Animals for Sale</h2>
  <p class="body-copy abs" style="left:225px;top:3320px;width:750px;text-align:center">It was popularised in the 1960s with the release of Lettersheet sheets containing Lorem Ipsum passages, and more recently with desktop publishing software like PageSetter including versions of Lorem Ipsum.</p>

  <div class="accent-green" style="left:107px;top:3433px;width:90px;height:110px"></div>
  <div class="accent-navy" style="left:1000px;top:3840px;width:92px;height:110px"></div>

  <div class="photo" style="left:125px;top:3450px;width:464px;height:222px;background:linear-gradient(180deg,#d8d6d0,#c4b59a 55%,#8e7a5a)" role="img" aria-label="Brown alpaca in a dry field"></div>
  <div class="photo" style="left:611px;top:3450px;width:222px;height:222px;background:linear-gradient(170deg,#c7a07a,#9a6a40 60%,#6a4a2a)" role="img" aria-label="Fawn alpaca close-up"></div>
  <div class="photo" style="left:850px;top:3450px;width:222px;height:222px;background:linear-gradient(170deg,#b9c7cf,#7a5a40 55%,#4a3a2c)" role="img" aria-label="Horse wearing a halter"></div>
  <div class="photo" style="left:125px;top:3714px;width:220px;height:222px;background:linear-gradient(170deg,#a9c4dc,#6b4a30 55%,#4f6a2e)" role="img" aria-label="Brown horse standing in grass"></div>
  <div class="photo" style="left:367px;top:3714px;width:222px;height:222px;background:linear-gradient(170deg,#aebfcc,#5a3a2a 55%,#3a2a1e)" role="img" aria-label="Dark horse in a paddock"></div>
  <div class="photo" style="left:611px;top:3714px;width:461px;height:222px;background:linear-gradient(180deg,#c4d6e6,#8fae5a 45%,#c9c0a6 70%,#6b8a3a)" role="img" aria-label="Flock of sheep in a fenced meadow"></div>

  <div class="abs" style="left:155px;top:3592px;color:#fff;font-weight:700;font-size:20px">Breed name<div style="font-size:13px;margin-top:8px">View full Descriptions</div></div>
  <div class="abs" style="left:630px;top:3614px;color:#fff;font-weight:700;font-size:13px">Breed name<div style="font-size:8px;margin-top:5px">View full Descriptions</div></div>
  <div class="abs" style="left:870px;top:3614px;color:#fff;font-weight:700;font-size:13px">Breed name<div style="font-size:8px;margin-top:5px">View full Descriptions</div></div>
  <div class="abs" style="left:145px;top:3878px;color:#fff;font-weight:700;font-size:13px">Breed name<div style="font-size:8px;margin-top:5px">View full Descriptions</div></div>
  <div class="abs" style="left:387px;top:3878px;color:#fff;font-weight:700;font-size:13px">Breed name<div style="font-size:8px;margin-top:5px">View full Descriptions</div></div>
  <div class="abs" style="left:640px;top:3856px;color:#fff;font-weight:700;font-size:20px">Breed name<div style="font-size:13px;margin-top:8px">View full Descriptions</div></div>
</section>

<!-- BLOG -->
<section class="blog">
  <div class="abs" style="left:0;top:4056px;width:1200px;height:540px;background:var(--navy)"></div>
  <svg class="abs" style="left:0;top:4530px" width="1200" height="70" viewBox="0 0 1200 70" preserveAspectRatio="none"><path d="M0 70 Q600 -20 1200 70 Z" fill="#fff"/></svg>
  <div class="abs" style="left:125px;top:4208px;color:var(--green);font-size:18px;font-weight:700">News</div>
  <h2 class="abs" style="left:125px;top:4238px;color:#fff;font-size:42px;font-weight:700">Latest Blogs Insight</h2>
  <p class="body-copy abs" style="left:125px;top:4305px;width:400px;color:#e6ebf2">Lorem Ipsum is simply dummy text of the printing and typesetting industry. Lorem Ipsum has been the industry's standard dummy text ever since the 1500s, when an unknown printer took a galley of type and scrambled it to make a type specimen book.</p>
  <div class="btn" style="left:125px;top:4445px;width:108px">See all</div>

  <div class="photo" style="left:639px;top:4200px;width:411px;height:300px;border-radius:10px;background:linear-gradient(160deg,#7c8a3a,#a9b85a 40%,#5a6a2a 80%,#2e3818)" role="img" aria-label="Woman in a sun hat beside a grey horse"></div>
  <div class="photo" style="left:1078px;top:4200px;width:122px;height:300px;border-radius:10px 0 0 10px;background:linear-gradient(170deg,#c9dcea,#9ab86a 55%,#6a8a3a)" role="img" aria-label="Horses on a hillside with a rider"></div>
  <svg class="abs" style="left:682px;top:4408px" width="18" height="18" viewBox="0 0 18 18"><rect x="1" y="3" width="16" height="14" rx="2" fill="#fff"/><rect x="1" y="3" width="16" height="4" fill="#ddd"/><rect x="4" y="1" width="2" height="4" fill="#fff"/><rect x="12" y="1" width="2" height="4" fill="#fff"/></svg>
  <div class="abs" style="left:726px;top:4411px;color:#fff;font-size:14px">Aug 11, 2018</div>
  <div class="abs" style="left:722px;top:4440px;width:210px;color:#fff;font-size:17px;line-height:1.35">Lorem Ipsum is simply dummy text of the</div>
</section>

<!-- FOOTER -->
<footer>
  <div class="abs" style="left:125px;top:4765px;display:flex;align-items:center;gap:8px;color:var(--navy);font-weight:700;font-size:26px;letter-spacing:1px"><span style="width:18px;height:18px;border-radius:50%;background:var(--green)"></span>MEADOWVALE</div>
  <div class="abs" style="left:360px;top:4730px;width:1px;height:115px;background:#b8bec6"></div>
  <p class="body-copy abs" style="left:403px;top:4730px;width:340px;color:var(--text)">Welcome to Meadowvale Alpacas, a picturesque haven nestled. Our farm is dedicated to raising and caring for a variety of animals, with a special focus on our beloved alpacas.</p>
  <p class="body-copy abs" style="left:403px;top:4836px;color:var(--text)">©2024 Meadowvale Alpacas. All rights reserved</p>
  <div class="abs" style="left:808px;top:4730px;width:1px;height:140px;background:#b8bec6"></div>
  <ul class="abs" style="left:833px;top:4712px;list-style:none;font-size:14px;line-height:37px;color:var(--navy)">
    <li>Home</li><li>Our story</li><li>The Farm</li><li>Animals History</li><li>For sale</li>
  </ul>
  <div class="abs" style="left:1020px;top:4730px;width:1px;height:140px;background:#b8bec6"></div>
  <div class="abs" style="left:1038px;top:4748px;width:34px;height:34px;border-radius:50%;background:var(--navy)"></div>
  <div class="abs" style="left:1038px;top:4792px;width:34px;height:34px;border-radius:50%;background:var(--navy)"></div>
  <div class="abs" style="left:1038px;top:4836px;width:34px;height:34px;border-radius:50%;background:var(--navy)"></div>

  <div class="abs" style="left:0;top:4967px;width:1200px;height:52px;background:var(--black);color:#fff;font-size:13px;display:flex;align-items:center;justify-content:center">© Copyright 2023&nbsp;<b>Meadowvale Alpacas</b>&nbsp;All rights reserved</div>
</footer>

</body>
</html>
```